Sparrow Haulage needs a business card design.

Design a double-sided business card for new freight business. On the front, would like to see our logo along with the following info:

Martin Obuya
CEO/FOUNDER
555-206-7142
martinobuya@sparrow-haulage.example

On the reverse side, we would like to use the graphic image of our logo only without the Sparrow Haulage name.

```html
<!DOCTYPE html>
<html lang="en">
<head>
<meta charset="utf-8">
<title>Sparrow Haulage – Business Card</title>
<link rel="stylesheet" href="https://fonts.googleapis.com/css2?family=Open+Sans:wght@400;700;800&display=swap">
<style>
  :root {
    --navy: #1c1959;
    --red: #b51f2a;
    --white: #ffffff;
    --backdrop: #3a3a3a;
    --card-w: 540px;
    --card-h: 309px;
  }
  * { margin: 0; padding: 0; box-sizing: border-box; }
  html, body { width: 1200px; height: 901px; overflow: hidden; }
  body {
    position: relative;
    background: var(--backdrop);
    font-family: "Open Sans", Arial, sans-serif;
  }
  .card {
    position: absolute;
    width: var(--card-w);
    height: var(--card-h);
    overflow: hidden;
    box-shadow: 0 10px 28px rgba(0,0,0,.45);
  }
  .card--back { left: 50px; top: 140px; background: var(--navy); }
  .card--front { left: 610px; top: 452px; background: var(--white); }

  .mark {
    position: absolute;
    left: 50%;
    top: 50%;
    width: 56px;
    height: 56px;
    transform: translate(-50%, -50%);
    border-radius: 50%;
    background: var(--red);
  }

  .brand {
    position: absolute;
    left: 34px;
    top: 70px;
    display: flex;
    align-items: center;
    gap: 12px;
    color: var(--navy);
    font-size: 22px;
    font-weight: 800;
    letter-spacing: 2px;
    text-transform: uppercase;
    line-height: 1;
  }
  .brand__dot { width: 24px; height: 24px; border-radius: 50%; background: var(--red); flex: none; }

  .wave { position: absolute; inset: 0; width: 100%; height: 100%; }

  .contact {
    position: absolute;
    right: 22px;
    top: 112px;
    text-align: right;
    color: var(--white);
  }
  .contact__name { font-size: 19px; font-weight: 700; line-height: 1.1; }
  .contact__role { font-size: 11px; font-weight: 400; letter-spacing: .5px; margin-bottom: 8px; }
  .contact__line {
    display: flex; justify-content: flex-end; align-items: center; gap: 6px;
    font-size: 10.5px; line-height: 1.55;
  }
  .contact__icon { width: 10px; height: 10px; flex: none; }
</style>
</head>
<body>

  <section class="card card--back" aria-label="Card reverse">
    <span class="mark" role="img" aria-label="Sparrow Haulage brand mark"></span>
  </section>

  <section class="card card--front" aria-label="Card front">
    <div class="brand"><span class="brand__dot"></span>Sparrow Haulage</div>

    <svg class="wave" viewBox="0 0 540 309" aria-hidden="true">
      <path fill="var(--red)" d="M0,207 C150,217 255,192 305,142 C355,88 430,68 540,58 L540,309 L0,309 Z"/>
      <path fill="var(--white)" d="M0,219 C150,229 258,204 308,154 C358,100 430,80 540,70 L540,309 L0,309 Z"/>
      <path fill="var(--navy)" d="M0,226 C150,236 262,210 312,160 C362,106 432,86 540,76 L540,309 L0,309 Z"/>
    </svg>

    <div class="contact">
      <p class="contact__name">Martin Obuya</p>
      <p class="contact__role">CEO/FOUNDER</p>
      <p class="contact__line">555-206-7142
        <svg class="contact__icon" viewBox="0 0 10 10" aria-hidden="true"><path fill="var(--white)" d="M2,0.5 L3.8,0.5 L4.3,3 L3,3.8 C3.6,5.2 4.8,6.4 6.2,7 L7,5.7 L9.5,6.2 L9.5,8 C9.5,9 8.8,9.5 8,9.5 C4,9.2 0.8,6 0.5,2 C0.5,1.2 1,0.5 2,0.5 Z"/></svg>
      </p>
      <p class="contact__line">martinobuya@sparrow-haulage.example
        <svg class="contact__icon" viewBox="0 0 10 10" aria-hidden="true"><rect x="0.5" y="2" width="9" height="6.5" fill="var(--white)"/><path d="M0.5,2 L5,5.8 L9.5,2" fill="none" stroke="var(--navy)" stroke-width="0.9"/></svg>
      </p>
      <p class="contact__line">www.sparrow-haulage.example
        <svg class="contact__icon" viewBox="0 0 10 10" aria-hidden="true"><circle cx="5" cy="5" r="4.5" fill="var(--white)"/><path d="M0.5,5 H9.5 M5,0.5 C3,3 3,7 5,9.5 M5,0.5 C7,3 7,7 5,9.5" fill="none" stroke="var(--navy)" stroke-width="0.7"/></svg>
      </p>
    </div>
  </section>

</body>
</html>
```